Animal Eye Clinic needs a Business card

We are a new veterinary ophthalmology practice (Ridgeline Pet Vision Care) and we need a business card designed. We only see animal eyes - we are not a regular veterinary clinic. We already have a logo. We are looking for a professional, good looking business card to hand out to our clients. We are looking for something simple but professional and contemporary. Our logo is likely the only picture/graphic that needs to be on the card.
Updates

Contact Information for Business Card

Delia Vossman, BSc, DVM, MSc, DipACVO
Veterinary Ophthalmologist

Phone: 250.418.3927
Email: ridgelinepetvisioncare@mailbox-example.net
Website: ridgelinepetvisioncare-example.net
Address: 1874 Thornbury Rd
Kelowna, BC, V1X 4M9

Colors

Designer to choose colors to be used in the design.

Requirements
Must have
• Our logo (attached)

```html
<!DOCTYPE html>
<html lang="en">
<head>
<meta charset="UTF-8">
<title>Ridgeline Pet Vision Care – Business Card</title>
<link href="https://fonts.googleapis.com/css2?family=Lato:wght@400;700;900&display=swap" rel="stylesheet">
<style>
  :root {
    --backdrop: #2b2b2c;
    --card: #161617;
    --card-edge: #1e1e1f;
    --teal: #0a9bb0;
    --white: #f1f1f1;
    --rule: #5a5a5a;
    --icon-ink: #161617;
  }
  * { box-sizing: border-box; margin: 0; padding: 0; }
  html, body {
    width: 1200px; height: 900px; overflow: hidden;
    background: var(--backdrop);
    font-family: 'Lato', sans-serif;
  }
  .stage {
    width: 1200px; height: 900px;
    display: flex; flex-direction: column; align-items: center; justify-content: center;
    gap: 40px;
  }
  .card {
    position: relative;
    width: 620px; height: 354px;
    background: linear-gradient(160deg, var(--card-edge), var(--card));
    overflow: hidden;
  }
  .card__band {
    position: absolute; left: 0; right: 0; bottom: 0;
    height: 12px; background: var(--teal);
  }

  /* Front */
  .card--front { display: flex; align-items: center; justify-content: center; }
  .brand { display: flex; align-items: center; gap: 16px; margin-top: -12px; }
  .brand__dot {
    width: 34px; height: 34px; border-radius: 50%;
    background: var(--teal);
  }
  .brand__name {
    color: var(--teal);
    font-weight: 900;
    font-size: 30px;
    letter-spacing: 0.5px;
    text-transform: uppercase;
  }

  /* Back */
  .card--back {
    display: flex; flex-direction: column; align-items: center;
    padding-top: 62px; text-align: center; color: var(--white);
  }
  .person__name {
    color: var(--teal); font-weight: 900; font-size: 19px; letter-spacing: 0.3px;
  }
  .person__name .person__creds { font-weight: 400; font-size: 14px; letter-spacing: 0.4px; }
  .person__title { font-size: 14px; margin-top: 3px; }
  .divider {
    display: flex; align-items: center; gap: 10px;
    width: 250px; margin: 10px 0 8px;
  }
  .divider::before, .divider::after {
    content: ""; flex: 1; height: 1px; background: var(--rule);
  }
  .icons { display: flex; gap: 5px; }
  .icons svg { width: 20px; height: 20px; display: block; }
  .contact { font-size: 15px; line-height: 1.38; }
  .contact__phone { font-size: 16px; }
  .rule { width: 250px; height: 1px; background: var(--rule); margin: 8px 0; }
  .address { font-size: 15px; }
</style>
</head>
<body>
<main class="stage">

  <section class="card card--front" aria-label="Business card front">
    <div class="brand">
      <span class="brand__dot"></span>
      <span class="brand__name">Ridgeline Pet Vision Care</span>
    </div>
    <div class="card__band"></div>
  </section>

  <section class="card card--back" aria-label="Business card back">
    <p class="person__name">DELIA VOSSMAN <span class="person__creds">BSC, DVM, MSC, DIPACVO</span></p>
    <p class="person__title">Veterinary Ophthalmologist</p>

    <div class="divider">
      <div class="icons">
        <svg viewBox="0 0 20 20" aria-label="Phone" role="img">
          <circle cx="10" cy="10" r="10" fill="var(--teal)"/>
          <path d="M6.5 5.5 L8.5 5.5 L9.2 8 L8 9 Q9 11.5 11 12 L12 10.8 L14.5 11.5 L14.5 13.5 Q9 14.5 6 8 Z" fill="var(--icon-ink)"/>
        </svg>
        <svg viewBox="0 0 20 20" aria-label="Email" role="img">
          <circle cx="10" cy="10" r="10" fill="var(--teal)"/>
          <rect x="5" y="6.5" width="10" height="7" fill="var(--icon-ink)"/>
          <path d="M5 6.5 L10 10.5 L15 6.5" fill="none" stroke="var(--teal)" stroke-width="1"/>
        </svg>
        <svg viewBox="0 0 20 20" aria-label="Website" role="img">
          <circle cx="10" cy="10" r="10" fill="var(--teal)"/>
          <circle cx="10" cy="10" r="5" fill="none" stroke="var(--icon-ink)" stroke-width="1.3"/>
          <ellipse cx="10" cy="10" rx="2" ry="5" fill="none" stroke="var(--icon-ink)" stroke-width="1.1"/>
          <line x1="5" y1="10" x2="15" y2="10" stroke="var(--icon-ink)" stroke-width="1.1"/>
        </svg>
      </div>
    </div>

    <div class="contact">
      <p class="contact__phone">250.418.3927</p>
      <p class="contact__email">ridgelinepetvisioncare@mailbox-example.net</p>
      <p class="contact__web">www.ridgelinepetvisioncare-example.net</p>
    </div>
    <div class="rule"></div>
    <p class="address">1874 Thornbury Rd Kelowna, BC, V1X 4M9</p>

    <div class="card__band"></div>
  </section>

</main>
</body>
</html>
```